Very new and innovative Web design for Property managers of Vacation rentals

We are looking for a new website design for travel agencies and property managers specialised on vacation rentals business, holiday villas and apartments.

The end users of this website are travellers who are looking for a vacation home for their next holiday: this is the reason why the website must be easy to use, attractive, professional, possibly elegant and focused on get new reservations.

This is a draft of our current website: https://intro3.kelumsito.com/
Please consider that we would like to have proposals with a totally different and innovative layout, surprise us!

These are the pages of the website:
• Homepage: feel free to redesign all the homepage as you wish, surprise us with something very new! Please consider that Property manager/Travel agencies usually want to have the opportunity to put in evidence groups of houses with specific characteristics (eg. villas with private swimming pool, apartment in big/small towns, villas with air co, etc…), destinations and tourist areas, and sometimes experiences or activities (please consider that the website layout must be suitable even if some of the previous sections are not used).
• Search page: we’d like to organise the results of the search page in three different ways:
o Grid
o Map
o List
• Property page: to illustrate the characteristics, descriptions, images, …. of the property. It is very important to put in evidence images of the property and to maintain the booking form (and the other call to action bottom – eg. whatsapp) always visible
• Custom pages: static pages composed usually by text, images and call to actions
• Contact us (general form)
• Info request (specific of a property form)
• Booking process
• Blog, organised in four pages:
o Home Page – introduction to the blog
o List of articles
o Single article
o Site Map (presentation of categories and sub-categories)

If possible, we’d prefer to receive the material in Adobe XD or similar so that we can obtain the three versions:
- smartphone
- tablet
- desktop

The website will be then developed in Bootstrap: as a result we’ll need the icons in SVG format (or the library used)

In attachment you can find the map of the website pages

```html
<!DOCTYPE html>
<html lang="en">
<head>
<meta charset="utf-8">
<title>Casalia Stays – Exclusive Villas in Italy</title>
<link rel="stylesheet" href="https://fonts.googleapis.com/css2?family=Josefin+Sans:wght@400;600;700&family=Lato:wght@400;700&display=swap">
<style>
:root{
  --green:#06b98a;
  --green-dark:#04a67b;
  --ink:#222;
  --text:#333;
  --muted:#555;
  --field:#f1f1f1;
  --band-top:#eef1f8;
  --band-bot:#c9d6ea;
  --footer:#2e2e2e;
  --white:#fff;
}
*{box-sizing:border-box;margin:0;padding:0}
html,body{width:1200px;height:3652px;overflow:hidden;background:var(--white)}
body{position:relative;font-family:'Lato',sans-serif;color:var(--text)}
.abs{position:absolute}
.heading{font-family:'Josefin Sans',sans-serif;font-weight:700;letter-spacing:1px;color:var(--ink);text-transform:uppercase;text-align:center}
.btn{display:inline-block;background:var(--green);color:#fff;font-family:'Josefin Sans',sans-serif;font-weight:600;letter-spacing:1px;text-transform:uppercase;border-radius:5px;text-align:center}

/* top bar */
.topbar{left:0;top:0;width:1200px;height:40px;background:var(--green);color:#fff;font-size:14px}
.topbar ul{list-style:none;position:absolute;right:173px;top:11px;display:flex;gap:26px}
.topbar li{display:flex;align-items:center;gap:6px}
.topbar svg{width:13px;height:13px;fill:#fff}
.flag{width:14px;height:9px;background:#c8d2e8;display:inline-block}

/* header */
.header{left:0;top:40px;width:1200px;height:113px;background:#fff}
.brand{position:absolute;left:173px;top:36px;display:flex;align-items:center;gap:10px;font-family:'Lato',sans-serif;font-size:38px;color:var(--green);font-weight:400}
.brand .dot{width:32px;height:32px;border-radius:50%;background:var(--green)}
.nav{position:absolute;right:173px;top:54px;display:flex;gap:20px;font-size:14.5px;letter-spacing:.5px;color:#333}

/* hero */
.hero{left:0;top:153px;width:1200px;height:563px;background:linear-gradient(180deg,#5d7ea3 0%,#9ab0c4 35%,#6c6a58 62%,#5b3a2c 100%)}
.hero-title{left:170px;top:262px;font-family:'Josefin Sans',sans-serif;font-weight:700;font-size:47px;line-height:57px;color:#fff;letter-spacing:1.5px}
.search-box{left:716px;top:121px;width:311px;height:360px;background:#fff;border-radius:6px;padding:12px}
.field{height:51px;background:var(--field);border-radius:5px;margin-bottom:9px;display:flex;align-items:center;justify-content:space-between;padding:0 14px;font-size:15px;color:#333}
.field svg{width:13px;height:13px;fill:#222}
.search-box .btn{width:115px;height:51px;line-height:53px;font-size:16px;margin-top:6px}

/* intro */
.intro-title{left:0;top:818px;width:1200px;font-size:29px}
.intro-text{left:178px;top:872px;width:844px;font-size:14px;line-height:25px;text-align:center;color:#333}

/* band */
.band{left:0;top:1092px;width:1200px;height:975px;background:linear-gradient(180deg,var(--band-top),var(--band-bot) 40%,#b9c9e2 60%)}
.band-arc{left:0;top:1092px;width:1200px;height:150px}
.feature{width:272px;height:272px;border-radius:50%;background:#fff;overflow:hidden;box-shadow:0 4px 14px rgba(0,0,0,.08);text-align:center}
.feature .photo{position:absolute;left:22px;top:0;width:228px;height:120px;border-radius:0 0 50% 50%/0 0 100% 100%}
.feature h3{position:absolute;top:132px;width:100%;font-family:'Lato',sans-serif;font-weight:400;font-size:22px;color:#222}
.feature p{position:absolute;top:170px;left:38px;width:196px;font-size:11px;line-height:19px;color:#333}

.rentals-bg{left:0;top:1489px;width:1200px;height:578px;background:linear-gradient(180deg,#7f9bb8 0%,#9fb3c6 30%,#6f6050 62%,#8b6b52 100%)}
.rentals-title{left:0;top:1393px;width:1200px;font-size:29px}
.card{width:264px;height:446px;background:#fff;border-radius:6px;padding:10px}
.card .photo{width:244px;height:205px;border-radius:5px}
.card h4{font-family:'Josefin Sans',sans-serif;font-weight:600;font-size:19px;letter-spacing:.5px;color:#222;margin:22px 5px 16px}
.row{display:flex;justify-content:space-between;font-family:'Josefin Sans',sans-serif;font-size:16px;color:#222;padding:10px 14px 10px 5px;border-bottom:1px solid #e6e6e6}
.card .btn{display:block;width:129px;height:44px;line-height:46px;font-size:14px;margin:26px auto 0}

/* blog */
.blog-title{left:0;top:2156px;width:1200px;font-size:29px}
.post{background:#fff;border-radius:6px;box-shadow:0 2px 12px rgba(0,0,0,.12)}
.post-big{left:173px;top:2242px;width:414px;height:459px;padding:10px;text-align:center}
.post-big .photo{width:394px;height:220px;border-radius:5px}
.post h5{font-family:'Josefin Sans',sans-serif;font-weight:600;font-size:19px;letter-spacing:.5px;color:#222}
.post-big h5{margin-top:26px}
.post-big p{font-size:12.5px;line-height:25px;color:#333;margin:10px 6px 0}
.post-big .btn{width:129px;height:44px;line-height:46px;font-size:14px;margin-top:20px}
.post-small{left:613px;width:414px;height:210px;padding:10px}
.post-small .photo{position:absolute;left:10px;top:10px;width:186px;height:190px;border-radius:5px}
.post-small .body{position:absolute;left:212px;top:24px;width:190px}
.post-small p{font-size:12px;line-height:25px;color:#333;margin-top:12px}
.post-small .btn{width:113px;height:42px;line-height:44px;font-size:14px;margin-top:10px}

/* CTA */
.cta{left:0;top:2819px;width:1200px;height:454px;background:linear-gradient(110deg,#6aa4d6 0%,#b8d5ea 30%,#8db8d6 55%,#6b89a8 80%,#51657e 100%)}
.cta-title{right:173px;top:110px;text-align:right;font-family:'Josefin Sans',sans-serif;font-weight:700;font-size:47px;line-height:63px;color:#fff;letter-spacing:1.5px}
.cta .btn{position:absolute;right:173px;top:268px;width:164px;height:60px;line-height:62px;font-size:18px}

/* footer */
.footer{left:0;top:3273px;width:1200px;height:315px;background:var(--footer);color:#fff}
.footer .brand{left:173px;top:124px;color:#fff;font-size:46px}
.footer .brand .dot{background:#fff;width:36px;height:36px}
.fcol{position:absolute;top:96px;font-size:14px;line-height:31.5px}
.fcol h6{font-family:'Josefin Sans',sans-serif;font-weight:600;font-size:16px;letter-spacing:1px;margin-bottom:12px;line-height:20px}
.bottombar{left:0;top:3588px;width:1200px;height:64px;background:var(--green);color:#fff;font-size:14px}
.bottombar .copy{position:absolute;left:0;width:1200px;top:23px;text-align:center}
.bottombar .code{position:absolute;right:80px;top:23px}
</style>
</head>
<body>

<div class="abs topbar">
  <ul>
    <li><svg viewBox="0 0 16 16"><path d="M6 3l5 5-5 5V10H0V6h6z M9 1h6v14H9v-2h4V3H9z"/></svg>Login</li>
    <li><svg viewBox="0 0 16 16"><path d="M8 15L1.5 8.5A4 4 0 0 1 8 3a4 4 0 0 1 6.5 5.5z"/></svg>Wish List(0)</li>
    <li><span class="flag"></span>Language</li>
  </ul>
</div>

<header class="abs header">
  <div class="brand"><span class="dot"></span>Casalia Stays</div>
  <nav class="nav"><span>HOME</span><span>SEARCH</span><span>PROPERTY</span><span>CUSTOM</span><span>CONTACT</span></nav>
</header>

<section class="abs hero" role="img" aria-label="Modern white villa with pool and wooden deck at dusk">
  <h1 class="abs hero-title">EXCLUSIVE<br>VILLAS IN ITALY</h1>
  <form class="abs search-box">
    <div class="field">Destination<svg viewBox="0 0 16 16"><path d="M8 0a5.5 5.5 0 0 0-5.5 5.5C2.5 10 8 16 8 16s5.5-6 5.5-10.5A5.5 5.5 0 0 0 8 0zm0 8a2.5 2.5 0 1 1 0-5 2.5 2.5 0 0 1 0 5z"/></svg></div>
    <div class="field">Check In<svg viewBox="0 0 16 16"><path d="M2 3h12v12H2z M4 0h2v4H4z M10 0h2v4h-2z" /><path d="M3 7h10v7H3z" fill="#f1f1f1"/><path d="M4 8h2v2H4zm3 0h2v2H7zm3 0h2v2h-2zM4 11h2v2H4zm3 0h2v2H7z"/></svg></div>
    <div class="field">Check Out<svg viewBox="0 0 16 16"><path d="M2 3h12v12H2z M4 0h2v4H4z M10 0h2v4h-2z" /><path d="M3 7h10v7H3z" fill="#f1f1f1"/><path d="M4 8h2v2H4zm3 0h2v2H7zm3 0h2v2h-2zM4 11h2v2H4zm3 0h2v2H7z"/></svg></div>
    <div class="field">Travelers<svg viewBox="0 0 16 16"><circle cx="8" cy="4.5" r="3.5"/><path d="M1 16c0-4 3-7 7-7s7 3 7 7z"/></svg></div>
    <span class="btn">SEARCH</span>
  </form>
</section>

<h2 class="abs heading intro-title">Looking for an exclusive holiday?</h2>
<p class="abs intro-text">Browse our vacation rental selections If you are looking for a real experiences, our portal is the right solution. Our vacation homes are all located in Italy and we take care of them and their owners at every time. Our goal is give to our guest authentic taste of holiday and our country. Our team is always ready to assure the best time and take care of you! Add a local experience to your stay with us: by diving into our local "network" you can have the unique chance to discover and travel our culture through the eye of a local...!</p>

<div class="abs band"></div>
<svg class="abs band-arc" viewBox="0 0 1200 150" preserveAspectRatio="none"><path d="M0 0H1200V0Q600 150 0 0Z" fill="#fff"/></svg>
<div class="abs rentals-bg" role="img" aria-label="Wooden deck beside a villa pool at evening"></div>

<div class="abs feature" style="left:172px;top:1034px">
  <div class="photo" role="img" aria-label="Contemporary luxury villa with garden" style="background:linear-gradient(180deg,#8fb2d8,#c9c7bf 60%,#6c8a4c)"></div>
  <h3>Luxury Villas</h3>
  <p>This selection of properties includes all the best rentals available. Most with private swimming pool with chef and maid services available.</p>
</div>
<div class="abs feature" style="left:461px;top:1056px;width:278px;height:278px">
  <div class="photo" role="img" aria-label="Illuminated modern villa at night" style="left:25px;background:linear-gradient(180deg,#2f4f8a,#c9a873 60%,#2c3e5c)"></div>
  <h3 style="top:140px">Experiences</h3>
  <p style="top:178px;left:50px;width:178px">Don't lve just a holiday but an experience! Let's discover our services.</p>
</div>
<div class="abs feature" style="left:756px;top:1034px">
  <div class="photo" role="img" aria-label="Villa with glowing blue pool at night" style="background:linear-gradient(180deg,#2c3447,#a78863 50%,#1d8fd6)"></div>
  <h3>Last Minute Deals</h3>
  <p style="top:168px">Browse all the last minute deals to browse the villas offering discounts for last minute arrivals.</p>
</div>

<h2 class="abs heading rentals-title">New villas and vacation rentals</h2>

<article class="abs card" style="left:173px;top:1497px">
  <div class="photo" role="img" aria-label="Modern villa with large swimming pool" style="background:linear-gradient(180deg,#9dbad6,#d2c9b6 45%,#1f8ed1 75%,#8a7a66)"></div>
  <h4>Agriturismo Le Rondini</h4>
  <div class="row"><span>Sleeps</span><span>7</span></div>
  <div class="row"><span>Bedrooms</span><span>2</span></div>
  <span class="btn">VIEW DETAILS</span>
</article>
<article class="abs card" style="left:468px;top:1497px">
  <div class="photo" role="img" aria-label="Classic stone villa with pool under blue sky" style="background:linear-gradient(180deg,#3f84d4,#c8c2b3 50%,#2a86d8 80%,#c9c4b8)"></div>
  <h4>Villa 2</h4>
  <div class="row"><span>Sleeps</span><span>4</span></div>
  <div class="row"><span>Bedrooms</span><span>3</span></div>
  <span class="btn">VIEW DETAILS</span>
</article>
<article class="abs card" style="left:763px;top:1497px">
  <div class="photo" role="img" aria-label="Pool surrounded by trees and sun loungers" style="background:linear-gradient(180deg,#4d6b34,#7d8f4c 45%,#4aa6dc 75%,#2d8ecf)"></div>
  <h4>Podere La Quercia</h4>
  <div class="row"><span>Sleeps</span><span>27</span></div>
  <div class="row"><span>Bedrooms</span><span>10</span></div>
  <span class="btn">VIEW DETAILS</span>
</article>

<h2 class="abs heading blog-title">Blog posts</h2>

<article class="abs post post-big">
  <div class="photo" role="img" aria-label="Dark-roofed modern house with pool at dusk" style="background:linear-gradient(180deg,#8aa4bf,#4b4e55 45%,#d9b377 70%,#6fb6d8)"></div>
  <h5>Nemo Enim Ipsam Voluptatem</h5>
  <p>Nam libero tempore, cum soluta nobis est eligendi optio cumque nihil impedit quo minus id quod maxime placeat facere possimus omnis voluptas.</p>
  <span class="btn">READ MORE</span>
</article>
<article class="abs post post-small" style="top:2242px">
  <div class="photo" role="img" aria-label="Glass-walled villa interior with wooden floor" style="background:linear-gradient(90deg,#3b3b3b,#cfd4d2 40%,#5f8a45 75%,#3a2a22)"></div>
  <div class="body">
    <h5>Nemo Enim Ipsam</h5>
    <p>Nam libero tempore, cum soluta nobis est eligendi optio cumque nihil impedit quos.</p>
    <span class="btn">READ MORE</span>
  </div>
</article>
<article class="abs post post-small" style="top:2490px">
  <div class="photo" role="img" aria-label="White cubic modern house against blue sky" style="background:linear-gradient(180deg,#6f9fd4,#e9ecee 45%,#9ca3a6 80%,#6d7a55)"></div>
  <div class="body">
    <h5>Nemo Enim Ipsam</h5>
    <p>Nam libero tempore, cum soluta nobis est eligendi optio cumque nihil impedit quos.</p>
    <span class="btn">READ MORE</span>
  </div>
</article>

<section class="abs cta" role="img" aria-label="Canopy daybed by an infinity pool overlooking the sea">
  <h2 class="abs cta-title">EXCLUSIVE<br>VILLAS IN ITALY</h2>
  <span class="btn">EXPLORE NOW</span>
</section>

<footer class="abs footer">
  <div class="brand"><span class="dot"></span>Casalia Stays</div>
  <div class="fcol" style="left:591px">
    <h6>COMPANY</h6>
    <div>Privacy Policies</div>
    <div>Reservation Policies</div>
    <div>Cookie Policy</div>
  </div>
  <div class="fcol" style="left:802px">
    <h6>CASALIA STAYS</h6>
    <div>via dei Tigli 7</div>
    <div>50012 Valdoro, Firenze (Italy)</div>
    <div>Phone: +39 055 0000123</div>
    <div>VAT Code: IT00000000000</div>
  </div>
</footer>
<div class="abs bottombar">
  <div class="copy">Copyrights @ 2021 Casalia Stays. All Rights Reserved.</div>
  <div class="code">C20</div>
</div>

</body>
</html>
```